Bloomtandem.com Greeting cards

We need a total of 15 digital greeting cards. in the following categories of life milestones. 3 of each to start.

1. Bar Mitzvah and Bat Mitzvah
2. Sweet 16
3. Babies Birth
4. Anniversary
5. Birthday

```html
<!DOCTYPE html>
<html lang="en">
<head>
<meta charset="utf-8">
<title>Sweet 16 Greeting Card</title>
<link rel="stylesheet" href="https://fonts.googleapis.com/css2?family=Questrial&family=Dancing+Script:wght@500;600&display=swap">
<style>
  :root {
    --petal-pink: #f8bfcb;
    --petal-light: #fcd9e0;
    --card-white: #ffffff;
    --ink-pink: #e4177b;
  }
  html, body {
    margin: 0;
    padding: 0;
    width: 1200px;
    height: 900px;
    overflow: hidden;
    background: var(--petal-pink);
  }
  .card {
    position: relative;
    width: 1200px;
    height: 900px;
    overflow: hidden;
  }
  .floral-backdrop {
    position: absolute;
    inset: 0;
    background:
      radial-gradient(ellipse at 25% 30%, var(--petal-light) 0%, transparent 55%),
      radial-gradient(ellipse at 70% 80%, var(--petal-light) 0%, transparent 50%),
      var(--petal-pink);
  }
  .message-panel {
    position: absolute;
    left: 621px;
    top: 17px;
    width: 560px;
    height: 866px;
    background: var(--card-white);
  }
  .greeting {
    position: absolute;
    margin: 0;
    color: var(--ink-pink);
    font-family: "Questrial", sans-serif;
    font-size: 19px;
    letter-spacing: 0.3px;
    white-space: nowrap;
  }
  .greeting-first {
    left: 40px;
    top: 224px;
  }
  .initial {
    font-size: 50px;
    line-height: 1;
    vertical-align: -6px;
    margin-right: 1px;
  }
  .greeting-second {
    left: 77px;
    top: 302px;
  }
  .headline {
    position: absolute;
    margin: 0;
    color: var(--ink-pink);
    font-family: "Dancing Script", cursive;
    font-weight: 600;
    white-space: nowrap;
    line-height: 1;
  }
  .headline-top {
    left: 84px;
    top: 366px;
    font-size: 62px;
  }
  .headline-main {
    left: 160px;
    top: 456px;
    font-size: 90px;
  }
</style>
</head>
<body>
  <main class="card">
    <div class="floral-backdrop" role="img" aria-label="Soft pink swirling leaf and petal pattern"></div>
    <section class="message-panel">
      <p class="greeting greeting-first"><span class="initial">O</span>n this very special day of yours,</p>
      <p class="greeting greeting-second">I wish you all the fun you can get....!</p>
      <h1 class="headline headline-top">A Very Happy</h1>
      <h2 class="headline headline-main">Sweet 16 !!</h2>
    </section>
  </main>
</body>
</html>
```